Australian Trucking Company Requires Professional Looking Stationary

We require a professional looking stationary design that incorporates our newly designed logo.

Our business, called "Brell Haulage Contracting", provides contracting work, transport and logistics to business in Western Australia particularly with links to the mining sector.

We are a small business looking to expand and our new logo and our new stationary will help develop our brand image in our market place.

Target Market(s)

Businesses and Corporation with links to the Mining Sector

Industry/Entity Type

Small Business

Requirements
Must have
• The letterhead must have the following details:
The new logo

Text saying: "Brell Holdings Pty Ltd (ACN 582 316 907) ATF The Brell Discretionary Trust T/AS"
"ABN 71 834 209 553"
Address "P.O Box 817 Wattlegrove WA, 6958"
Phone: 08 9352 7140
Email: brellhaul@mailbox-example.com.au

The text on the letterhead should be editable as the details are likely to change in the near future. Provision should be made for a website address all though one isn't available at the moment.

The styling, layout and font text is entirely up to the designer.

```html
<!DOCTYPE html>
<html lang="en">
<head>
<meta charset="utf-8">
<title>Brell Haulage Contracting – Business Cards</title>
<link href="https://fonts.googleapis.com/css2?family=Open+Sans:wght@400;600;700&display=swap" rel="stylesheet">
<style>
  :root {
    --backdrop: #e8e5e1;
    --card-white: #ffffff;
    --card-grey: #dcdcdc;
    --brand-red: #9b1c22;
    --mark-grey: #6a6a6a;
    --text-dark: #3f3f3f;
    --text-body: #4a4a4a;
    --rule: #b5b5b5;
  }
  * { margin: 0; padding: 0; box-sizing: border-box; }
  html, body {
    width: 1200px; height: 407px; overflow: hidden;
    background: var(--backdrop);
    font-family: "Open Sans", sans-serif;
  }
  .canvas { position: relative; width: 1200px; height: 407px; }

  .card {
    position: absolute; top: 60px;
    width: 528px; height: 288px;
    box-shadow: 0 2px 6px rgba(0,0,0,0.18);
  }
  .card--front {
    left: 58px;
    background: radial-gradient(ellipse at 50% 40%, var(--card-white) 0%, #f1f1f1 45%, var(--card-grey) 100%);
  }
  .card--back { left: 638px; background: var(--card-white); }

  .brand {
    position: absolute; top: 40px; left: 78px;
    display: flex; align-items: center; gap: 20px;
  }
  .brand__square { width: 72px; height: 72px; background: var(--mark-grey); }
  .brand__name {
    color: var(--brand-red);
    font-weight: 700; font-size: 25px; line-height: 27px;
    text-transform: uppercase; letter-spacing: 0.5px;
  }

  .holder {
    position: absolute; top: 162px; left: 0; width: 100%;
    text-align: center; color: var(--brand-red);
    font-size: 13px;
  }
  .holder__name { font-weight: 700; font-size: 15px; }

  .details { position: absolute; top: 212px; left: 0; width: 100%; font-size: 12.5px; line-height: 19px; color: var(--text-body); }
  .details__address { position: absolute; right: 306px; text-align: right; white-space: nowrap; }
  .details__rule { position: absolute; left: 254px; top: 2px; width: 1px; height: 56px; background: var(--rule); }
  .details__contact { position: absolute; left: 280px; white-space: nowrap; list-style: none; }
  .details__label { display: inline-block; width: 18px; }

  .web {
    position: absolute; top: 252px; left: 0; width: 100%;
    text-align: center; font-weight: 700; font-size: 13px;
    letter-spacing: 3px; color: var(--text-dark);
  }
</style>
</head>
<body>
<main class="canvas">
  <section class="card card--front">
    <div class="brand">
      <span class="brand__square"></span>
      <p class="brand__name">Brell<br>Haulage<br>Contracting</p>
    </div>
    <p class="holder"><span class="holder__name">Your Name</span>, Title</p>
    <div class="details">
      <address class="details__address" style="font-style: normal;">
        P.O Box 817<br>
        Wattlegrove WA, 6958<br>
        ABN 71 834 209 553
      </address>
      <span class="details__rule"></span>
      <ul class="details__contact">
        <li><span class="details__label">P:</span>08 9352 7140</li>
        <li><span class="details__label">E:</span>brellhaul@mailbox-example.com.au</li>
        <li><span class="details__label">W:</span>www.brellhaulage.com.au</li>
      </ul>
    </div>
  </section>

  <section class="card card--back">
    <div class="brand">
      <span class="brand__square"></span>
      <p class="brand__name">Brell<br>Haulage<br>Contracting</p>
    </div>
    <p class="web">www.brellhaulage.com.au</p>
  </section>
</main>
</body>
</html>
```